New Website

New website is to be the same as Amber Lantern.

Website needs to be fully functional, with only text and logo to be added by client at a later date.

Logo has been added for reference.

```html
<!DOCTYPE html>
<html lang="en">
<head>
<meta charset="utf-8">
<title>Veloran – The Right Expert, Right Now</title>
<link href="https://fonts.googleapis.com/css2?family=Roboto:ital,wght@0,300;0,400;0,500;0,700;1,400&display=swap" rel="stylesheet">
<style>
:root{
  --blue:#3d5db5;
  --blue-dark:#2c4a8f;
  --navy:#28406f;
  --cyan:#5cc4e4;
  --cyan-btn:#56c6e8;
  --ink:#222;
  --muted:#444;
  --grey-band:#e6e7ea;
  --grey-light:#f6f6f7;
  --white:#fff;
}
*{margin:0;padding:0;box-sizing:border-box}
html,body{width:1200px;height:2778px;overflow:hidden}
body{position:relative;background:var(--white);font-family:'Roboto',sans-serif;color:var(--ink)}
.abs{position:absolute}
.center{text-align:center}

/* header */
.topbar{left:0;top:61px;width:1200px;height:37px;background:var(--blue)}
.brand{left:190px;top:22px;font-size:34px;font-weight:400;color:var(--blue);letter-spacing:1px;line-height:1}
.nav a{position:absolute;top:34px;font-size:15px;color:var(--ink);text-decoration:none}
.btn-sm{position:absolute;top:26px;height:24px;background:var(--blue);color:var(--white);font-size:12px;display:flex;align-items:center;justify-content:center}
.or{left:918px;top:31px;font-size:11px;color:#555}
.make-expert{left:654px;top:61px;width:174px;height:37px;background:var(--navy);color:var(--white);font-size:15px;display:flex;align-items:center;justify-content:center;gap:8px}
.find-expert{left:837px;top:61px;width:180px;height:46px;background:var(--cyan-btn);color:var(--white);font-size:16px;display:flex;align-items:center;justify-content:center;gap:10px}

/* hero */
.hero-photo{left:537px;top:98px;width:663px;height:412px;background:linear-gradient(90deg,#fff 0%,#eceef1 30%,#d7dadf 70%,#c8ccd2 100%)}
.hero-title{left:204px;top:190px;font-size:31px;line-height:37px;font-weight:400;color:var(--ink)}
.hero-sub{left:204px;top:296px;font-size:20px;color:var(--ink)}
.btn{position:absolute;height:24px;background:var(--blue);color:var(--white);font-size:12px;display:flex;align-items:center;justify-content:center;gap:6px}
.dots{left:279px;top:436px;display:flex;gap:4px}
.dots span{width:8px;height:8px;border-radius:50%;background:#8a8f99}

/* testimonial */
.testimonial{left:0;top:487px;width:1200px;height:280px;background:var(--blue);overflow:hidden}
.testimonial-title{left:0;top:62px;width:1200px;font-size:25px;color:var(--white);font-weight:400}
.quote{left:295px;top:114px;width:610px;font-size:13.5px;line-height:21px;font-style:italic;color:#e5eaf7}
.quote-name{left:0;top:206px;width:1200px;font-size:17px;color:var(--white)}
.quote-role{left:0;top:227px;width:1200px;font-size:10px;color:#dfe5f5}

/* video */
.video-section{left:0;top:767px;width:1200px;height:340px;background:var(--grey-light)}
.section-title{left:0;width:1200px;font-weight:400;color:var(--ink)}
.video{left:291px;top:869px;width:618px;height:276px;background:linear-gradient(135deg,#dfe7ef,#c7cdd4 50%,#a9b3bd);border:3px solid var(--white);box-shadow:0 6px 10px rgba(0,0,0,.2)}
.grey-band{left:0;top:1107px;width:1200px;height:230px;background:var(--grey-band)}

/* experts */
.expert-photo{position:absolute;top:1259px;width:135px;height:134px;background:linear-gradient(160deg,#e8ebee,#b9c0c7);border:3px solid var(--white);box-shadow:0 1px 4px rgba(0,0,0,.25)}
.expert-name{position:absolute;top:1415px;font-size:17px;font-weight:700;color:var(--blue)}
.expert-role{position:absolute;top:1436px;font-size:13px;line-height:15px;color:var(--ink)}
.qual-band{left:0;top:1491px;width:1200px;height:176px;background:var(--grey-band)}
.qual-text{left:232px;top:1526px;width:736px;font-size:17.5px;line-height:21px;color:var(--ink)}

/* how it works */
.how-sub{left:0;top:1759px;width:1200px;font-size:13px;color:var(--ink)}
.step-title{position:absolute;top:1935px;width:240px;font-size:23px;line-height:29px;font-weight:400;color:var(--ink);text-align:center}
.step-text{position:absolute;top:2012px;width:190px;font-size:11.5px;line-height:17px;color:var(--ink);text-align:center}
.slash{position:absolute;top:1942px;width:2px;height:54px;background:var(--blue);transform:rotate(20deg)}

/* footer */
.col{position:absolute;top:2215px;height:493px}
.col-about{left:181px;width:278px;background:var(--cyan)}
.col-thinking{left:463px;width:276px;background:var(--blue)}
.col-help{left:743px;width:276px;background:var(--navy)}
.footer-links a{display:block;font-size:33px;line-height:46px;color:var(--white);text-decoration:none;font-weight:400}
.col-heading{color:var(--white);font-weight:400}
.post{color:var(--white);font-size:11px;line-height:15px;text-align:center}
.post b,.post i{display:block;font-size:10px}
.help-text{font-size:11px;line-height:16px;color:#e3e8f3}
.social{display:flex;gap:4px}
.social span{width:34px;height:34px;border-radius:50%;display:block}
.copyright{left:181px;top:2736px;font-size:11px;color:var(--ink)}
</style>
</head>
<body>

<header>
  <div class="abs topbar"></div>
  <div class="abs brand">VELORAN</div>
  <nav class="nav">
    <a style="left:467px">How it Works</a>
    <a style="left:574px">Products</a>
    <a style="left:652px">Blog</a>
    <a style="left:704px">Help</a>
  </nav>
  <div class="btn-sm" style="left:837px;width:70px">Sign In</div>
  <div class="abs or">OR</div>
  <div class="btn-sm" style="left:944px;width:73px">Register</div>
  <div class="abs make-expert">
    <svg width="10" height="7" viewBox="0 0 10 7"><path d="M0 0h10L5 7z" fill="#fff"/></svg>Make Me An Expert
  </div>
  <div class="abs find-expert">
    <svg width="18" height="18" viewBox="0 0 18 18"><circle cx="7.5" cy="7.5" r="5.5" fill="none" stroke="#fff" stroke-width="2.4"/><path d="M11.5 11.5l5 5" stroke="#fff" stroke-width="2.6" stroke-linecap="round"/></svg>Find Your Expert
  </div>
</header>

<section class="hero">
  <div class="abs hero-photo" role="img" aria-label="Smiling consultant in shirt and tie at a laptop in a bright meeting room"></div>
  <h1 class="abs hero-title">The Right Expert,<br>Right Now™</h1>
  <p class="abs hero-sub">Consulting Made Simple</p>
  <div class="btn" style="left:204px;top:357px;width:181px">Browse Business Categories <span>›</span></div>
  <div class="abs dots"><span></span><span></span><span></span></div>
</section>

<section class="abs testimonial">
  <svg class="abs" style="left:0;top:0" width="1200" height="280" viewBox="0 0 1200 280">
    <path d="M215 128l-12 13 12 13" fill="none" stroke="#fff" stroke-width="2.5"/>
    <path d="M985 128l12 13-12 13" fill="none" stroke="#fff" stroke-width="2.5"/>
  </svg>
  <h2 class="abs testimonial-title center">What Clients Are Saying</h2>
  <p class="abs quote center">I felt this session was on target and the solutions we discussed are real candidates. We are only one discussion away from recommending a winning plan. Owen Halvik was articulate, knowledgeable, experienced, and concise. Very helpful!</p>
  <p class="abs quote-name center">Mara Linwood</p>
  <p class="abs quote-role center">—CEO, the copper bench</p>
</section>

<section>
  <div class="abs video-section"></div>
  <div class="abs grey-band"></div>
  <h2 class="abs section-title center" style="top:800px;font-size:28px">Watch The Video</h2>
  <div class="abs video" role="img" aria-label="Video still of a business team gathered around a table reviewing documents"></div>
  <svg class="abs" style="left:570px;top:989px" width="60" height="36" viewBox="0 0 60 36"><rect width="60" height="36" rx="4" fill="#222" opacity=".85"/><path d="M24 10l14 8-14 8z" fill="#fff"/></svg>

  <h2 class="abs section-title center" style="top:1188px;font-size:24px">Introducing Your Business Expert Network</h2>
  <div class="expert-photo" style="left:228px" role="img" aria-label="Portrait of expert Dana Pelloway"></div>
  <div class="expert-photo" style="left:431px" role="img" aria-label="Portrait of expert Robin Ashcroft"></div>
  <div class="expert-photo" style="left:635px" role="img" aria-label="Portrait of expert Richard Fennimore"></div>
  <div class="expert-photo" style="left:839px" role="img" aria-label="Portrait of expert Jess Holloran"></div>

  <p class="expert-name" style="left:228px">Dana Pelloway</p>
  <p class="expert-role" style="left:228px">CEO • Northfield Works, Inc.<br>Cloudmere Services</p>
  <p class="expert-name" style="left:431px">Robin Ashcroft</p>
  <p class="expert-role" style="left:431px">Senior Director<br>Market Research</p>
  <p class="expert-name" style="left:635px">Richard Fennimore</p>
  <p class="expert-role" style="left:635px">Principal<br>Strategic Messaging</p>
  <p class="expert-name" style="left:839px">Jess Holloran</p>
  <p class="expert-role" style="left:839px">Chief Operating Officer<br>Manufacturing Strategy</p>

  <div class="abs qual-band"></div>
  <p class="abs qual-text center">All of our experts meet high qualification requirements and undergo rigorous testing for their specific skills and consulting abilities. Learn more about how experts are chosen. If you think you have what it takes, become an expert today.</p>
  <div class="btn" style="left:541px;top:1613px;width:116px">See All Experts <span>›</span></div>
</section>

<section>
  <h2 class="abs section-title center" style="top:1709px;font-size:24px">How it Works</h2>
  <p class="abs how-sub center">Find an Expert who's just right for your business need. Your Expert Package includes:</p>

  <svg class="abs" style="left:290px;top:1833px" width="74" height="74" viewBox="0 0 74 74">
    <path d="M6 14h50v50l-10 6H6z" fill="none" stroke="#3d5db5" stroke-width="5"/>
    <path d="M22 4v22" stroke="#3d5db5" stroke-width="5" stroke-linecap="round"/>
    <path d="M40 8l14 30" stroke="#3d5db5" stroke-width="5" stroke-linecap="round"/>
  </svg>
  <svg class="abs" style="left:562px;top:1833px" width="76" height="74" viewBox="0 0 76 74">
    <rect x="30" y="2" width="16" height="20" rx="7" fill="#3d5db5"/>
    <rect x="24" y="22" width="28" height="20" fill="#3d5db5"/>
    <rect x="2" y="42" width="72" height="8" fill="#3d5db5"/>
    <path d="M16 52h44l-6 20H22z" fill="#3d5db5"/>
  </svg>
  <svg class="abs" style="left:832px;top:1830px" width="82" height="80" viewBox="0 0 82 80">
    <circle cx="41" cy="10" r="7" fill="#3d5db5"/><circle cx="12" cy="52" r="7" fill="#3d5db5"/><circle cx="70" cy="52" r="7" fill="#3d5db5"/>
    <circle cx="41" cy="44" r="11" fill="none" stroke="#3d5db5" stroke-width="6" stroke-dasharray="5 3"/>
    <path d="M2 76a10 12 0 0 1 20 0zM60 76a10 12 0 0 1 20 0zM31 30a10 10 0 0 1 20 0z" fill="#3d5db5"/>
    <path d="M24 24l-8 14M58 24l8 14M26 72h30" stroke="#3d5db5" stroke-width="3"/>
  </svg>

  <h3 class="step-title" style="left:206px">Pre-Session<br>Discovery</h3>
  <h3 class="step-title" style="left:480px">One+-On-One<br>Session</h3>
  <h3 class="step-title" style="left:752px">Post-Session<br>Options</h3>
  <div class="slash" style="left:455px"></div>
  <div class="slash" style="left:736px"></div>
  <p class="step-text" style="left:231px">Lorem Ipsum has been the industry's standard dummy text ever since the 1500s, when an unknown printer took a galley of type and scrambled it to make a type specimen book.</p>
  <p class="step-text" style="left:505px">Lorem Ipsum has been the industry's standard dummy text ever since the 1500s, when an unknown printer took a galley of type and scrambled it to make a type specimen book.</p>
  <p class="step-text" style="left:777px">Lorem Ipsum has been the industry's standard dummy text ever since the 1500s, when an unknown printer took a galley of type and scrambled it to make a type specimen book.</p>
  <div class="btn" style="left:541px;top:2143px;width:116px">See How it work <span>›</span></div>
</section>

<footer>
  <div class="col col-about">
    <nav class="abs footer-links" style="left:22px;top:34px">
      <a>About Us</a><a>Our Team</a><a>Legal</a><a>Contact Us</a>
    </nav>
  </div>
  <div class="col col-thinking">
    <h2 class="abs col-heading center" style="left:0;top:38px;width:276px;font-size:28px;line-height:34px">What We're<br>Thinking</h2>
    <div class="abs post" style="left:36px;top:138px;width:204px">“Lorem Ipsum is simply dummy text of the printing and typesetting industry.”<b>Monday, January 12</b><i><b>Tessa Brannock</b></i></div>
    <div class="abs post" style="left:36px;top:238px;width:204px">“Lorem Ipsum is simply dummy text of the printing and typesetting industry. Lorem Ipsum has been the industry's standard dummy text ever since the 1500s, when an unknown printer took a galley of type and scrambled it to make a type specimen book. It has survived not only five centuries, but also the leap into electronic typesetting, remaining essentially unchanged.”<br><b>Monday, January 12</b><i><b>Owen Halvik</b></i></div>
  </div>
  <div class="col col-help">
    <h2 class="abs col-heading" style="left:17px;top:40px;font-size:29px">Need Help?</h2>
    <p class="abs help-text" style="left:17px;top:92px;width:230px">Amber Lantern is committed to providing exceptional cloud-based consulting. If you need help with any aspect of the Amber Lantern experience, please send us a note and we will reply promptly. Or feel free to call our support line between 9am and 5pm Pacific Time.</p>
    <h2 class="abs col-heading" style="left:17px;top:232px;font-size:30px">Contact Us</h2>
    <p class="abs help-text" style="left:17px;top:284px;font-size:10.5px;line-height:14px">Amber Lantern, Inc.<br>support@amberlantern.example</p>
    <h2 class="abs col-heading" style="left:17px;top:344px;font-size:29px">Follow us on</h2>
    <div class="abs social" style="left:17px;top:393px" aria-label="Social links">
      <span style="background:#3b5aa6"></span><span style="background:#35a9e4"></span><span style="background:#d8412f"></span><span style="background:#e0302a"></span><span style="background:#1f79b5"></span>
    </div>
  </div>
  <p class="abs copyright">© 2015 Veloran. Terms of Use and Privacy Policy</p>
</footer>

</body>
</html>
```